Retail/Wholesale website graphic template

I need to design a new graphic template for a website for a client. The website will be a retail/wholesale company site with most pages dedicated to presentation. There will also be an online store and a blog. However, you don't need to worry about those. All I need from you is a graphic template for a generic site page.

It will need to include standard UI elements, in case I need those. I am attaching a more detailed assignment in .docx format.

The logo is also attached.

Target Market(s)

small business owners, (occasional) retail customers

Industry/Entity Type

Wholesale

Number of Pages Required

1 page

Font styles to use
Serif
Sans Serif

Colors
ec1f27
474747

Requirements
Must have
• must match logo, be clean, minimal and with slightly larger text size
Should not have
• must not be modern-looking where you have to scroll and scroll and scroll to get to the bottom of the homepage. most of my visitors are "old" people, they do not get this type of design.

```html
<!DOCTYPE html>
<html lang="en">
<head>
<meta charset="utf-8">
<title>Marlow Imports — Retail &amp; Wholesale</title>
<link href="https://fonts.googleapis.com/css2?family=Roboto:wght@300;400;500;700&display=swap" rel="stylesheet">
<style>
:root{
  --red:#ec1f27;
  --red-deep:#c8101a;
  --red-soft:#f2425a;
  --ink:#474747;
  --dark:#222;
  --muted:#777;
  --line:#d6d6d6;
  --paper:#fff;
  --foot:#e9e9e9;
}
*{margin:0;padding:0;box-sizing:border-box}
html,body{width:1200px;height:3805px;overflow:hidden}
body{position:relative;font-family:"Roboto",Arial,sans-serif;color:var(--ink);background:var(--paper)}
.abs{position:absolute}
/* top bar */
.topbar{left:0;top:0;width:1200px;height:33px;background:var(--red);color:#fff;font-size:15px;display:flex;justify-content:flex-end;align-items:center;gap:28px;padding-right:60px}
.topbar span{display:flex;align-items:center;gap:6px;white-space:nowrap}
/* hero */
.hero{left:0;top:33px;width:1200px;height:723px;background:linear-gradient(180deg,#4a4d55 0%,#6b6a66 45%,#3d3b38 100%)}
.hero-cut{left:0;top:640px;width:1200px;height:120px}
.brand-box{left:107px;top:33px;width:268px;height:119px;background:#fff;display:flex;align-items:center;justify-content:center}
.brand{font-size:46px;font-weight:500;color:var(--red);letter-spacing:3px;display:flex;align-items:center;gap:12px}
.brand i{width:14px;height:14px;background:var(--red);display:block}
.nav{left:420px;top:86px;display:flex;gap:30px;color:#fff;font-size:16px;font-weight:500}
.nav a{color:#fff;text-decoration:none}
.dropdown{left:431px;top:140px;width:198px;height:124px;background:var(--red);padding:18px 0 0 34px;color:#fff;font-size:15px;line-height:31px;font-weight:500}
.hero-title{left:0;top:305px;width:1200px;text-align:center;color:#fff;font-size:52px;font-weight:500;letter-spacing:1px}
.hero-sub{left:0;top:378px;width:1200px;text-align:center;color:#fff;font-size:29px;font-weight:500;line-height:36px}
.hero-dots{left:545px;top:650px;display:flex;gap:8px;align-items:center}
.dot{width:10px;height:10px;border-radius:50%;background:#ddd}
.arrow-dot{width:22px;height:22px;border-radius:50%;background:#fff}
/* about */
.about-art{left:140px;top:770px;width:418px;height:397px;background:linear-gradient(135deg,#d8e6ee,#6ea1b7 55%,#f2b63a);border-radius:8px}
h2{font-weight:500;font-size:38px}
.about-h{left:609px;top:810px;color:var(--red)}
.about-p{left:609px;top:866px;width:470px;font-size:14px;line-height:25px;color:#555}
.about-p p{margin-bottom:14px}
/* why */
.why-band{left:0;top:1180px;width:1200px;height:550px}
.why-h{left:130px;top:1302px;color:#fff}
.why-intro{left:130px;top:1352px;width:500px;color:#fff;font-size:14px;line-height:22px}
.why-list{left:130px;top:1412px;color:#fff;font-size:16px;line-height:33px;list-style:none}
.why-list li::before{content:"›";font-weight:700;margin-right:10px}
.why-photo{left:635px;top:1236px;width:446px;height:446px;border-radius:50%;background:linear-gradient(160deg,#c9d9e6,#8a9e76 45%,#b87a45);border:6px solid #fff;box-shadow:0 6px 20px rgba(0,0,0,.3)}
/* process */
.process-h{left:0;top:1760px;width:1200px;text-align:center;color:var(--dark)}
.step-ring{width:132px;height:132px;border-radius:50%;background:#fff;border:2px solid #e6e6e6;display:flex;align-items:center;justify-content:center;box-shadow:0 2px 8px rgba(0,0,0,.08)}
.step-ring.active{background:var(--red);border-color:var(--red)}
.step-line{left:261px;top:2016px;width:668px;height:2px;background:var(--line)}
.step-node{width:20px;height:20px;border-radius:50%;background:#fff;border:2px solid #999}
.step-title{width:340px;text-align:center;font-size:20px;font-weight:500;color:var(--dark)}
.step-text{width:340px;text-align:center;font-size:15px;line-height:22px;color:#666}
/* news */
.news-band{left:0;top:2175px;width:1200px;height:710px}
.news-h{left:0;top:2323px;width:1200px;text-align:center;color:#fff}
.card{top:2395px;width:300px;height:294px;color:#fff}
.card.photo{background:linear-gradient(180deg,#8c6a4e,#5b4a3c 60%,#2c2723)}
.card.photo .cap{position:absolute;left:26px;bottom:22px;font-size:16px;line-height:21px}
.card.feature{background:var(--red);padding:52px 30px 0;font-size:14px}
.card.feature .date{font-size:13px;margin-bottom:14px}
.card.feature h3{font-size:17px;font-weight:500;line-height:22px;margin-bottom:12px}
.card.feature p{font-size:12px;line-height:17px;opacity:.9}
.card.feature .more{display:inline-block;margin-top:26px;font-size:12px;font-weight:700;border-bottom:2px solid #fff;padding-bottom:4px}
/* testimonials */
.testi-h{left:0;top:2883px;width:1200px;text-align:center;color:var(--red);font-size:32px}
.quote-card{top:2961px;width:470px;height:228px;background:#fff;box-shadow:0 2px 14px rgba(0,0,0,.14);padding:42px 40px 0 70px}
.quote-card .q{font-size:14px;line-height:26px;color:#888;font-style:italic;position:relative}
.quote-card .q::before{content:"“";position:absolute;left:-44px;top:-14px;font-size:60px;color:#ccc;font-style:normal}
.author{display:flex;align-items:center;gap:14px;margin-top:26px}
.avatar{width:48px;height:48px;border-radius:50%;background:linear-gradient(135deg,#e9c8a7,#b88460)}
.author b{display:block;font-size:15px;font-weight:500;color:var(--dark)}
.author small{font-size:12px;color:#999}
.testi-dots{left:541px;top:3223px;display:flex;gap:8px;align-items:center}
.testi-dots .dot{background:#bbb}
.testi-dots .arrow-dot{background:#999}
/* footer */
.footer{left:0;top:3300px;width:1200px;height:505px}
.foot-brand{left:121px;top:3385px;font-size:42px;font-weight:500;color:var(--red);letter-spacing:3px;display:flex;align-items:center;gap:12px}
.foot-brand i{width:14px;height:14px;background:var(--red);display:block}
.foot-col{top:3496px}
.foot-col h4{font-size:19px;font-weight:500;color:var(--dark);margin-bottom:14px}
.foot-col ul{list-style:none;font-size:14px;line-height:27px;color:#555}
.contact li{display:flex;align-items:center;gap:12px;line-height:36px;white-space:nowrap}
.foot-rule{left:127px;top:3709px;width:940px;height:1px;background:#c9c9c9}
.copy{left:127px;top:3740px;font-size:13px;color:#555}
.social{left:921px;top:3727px;display:flex;gap:6px}
.social span{width:37px;height:37px;border-radius:50%;border:2px solid #555;display:block}
</style>
</head>
<body>

<header>
  <div class="abs topbar">
    <span><svg width="12" height="12" viewBox="0 0 24 24"><path fill="#fff" d="M6.6 10.8a15 15 0 0 0 6.6 6.6l2.2-2.2a1 1 0 0 1 1-.25 11.4 11.4 0 0 0 3.6.57 1 1 0 0 1 1 1V20a1 1 0 0 1-1 1A17 17 0 0 1 3 4a1 1 0 0 1 1-1h3.5a1 1 0 0 1 1 1c0 1.25.2 2.45.57 3.6a1 1 0 0 1-.25 1z"/></svg>(685) 555 0148</span>
    <span><svg width="14" height="11" viewBox="0 0 24 18"><rect x="1" y="1" width="22" height="16" fill="none" stroke="#fff" stroke-width="2"/><path d="M1 1l11 9 11-9" fill="none" stroke="#fff" stroke-width="2"/></svg>hello@marlowimports.com</span>
    <span><svg width="12" height="13" viewBox="0 0 24 24"><circle cx="12" cy="7" r="5" fill="#fff"/><path d="M2 24a10 10 0 0 1 20 0z" fill="#fff"/></svg>Profile</span>
  </div>

  <div class="abs hero" role="img" aria-label="Photo of a wholesale store aisle with stocked shelves"></div>
  <svg class="abs hero-cut" width="1200" height="120" viewBox="0 0 1200 120"><polygon points="0,116 1200,7 1200,120 0,120" fill="#fff"/></svg>

  <div class="abs brand-box"><div class="brand"><i></i>MARLOW</div></div>

  <nav class="abs nav">
    <a>ABOUT US</a><a>WHY CHOOSE US</a><a>OUR PROCESS</a><a>NEWS &amp; BLOGS</a><a>TESTIMONIALS</a>
  </nav>
  <div class="abs dropdown">OUR HISTORY<br>WHY US<br>OUR TEAM</div>

  <h1 class="abs hero-title">RETAIL &amp; WHOLE SALE IMPORT</h1>
  <p class="abs hero-sub">PROIN NULLA ARCU NONUMMY LUCTUS DICTUM<br>EGET FERMENTUM ET LOREM NUNC</p>
  <svg class="abs" style="left:583px;top:476px" width="34" height="22" viewBox="0 0 34 22"><path d="M3 3l14 14L31 3" fill="none" stroke="#fff" stroke-width="5"/></svg>
  <div class="abs hero-dots">
    <span class="arrow-dot"></span><span class="dot" style="background:#fff"></span><span class="dot"></span><span class="dot"></span><span class="dot"></span><span class="arrow-dot"></span>
  </div>
</header>

<section class="about">
  <div class="abs about-art" role="img" aria-label="Isometric illustration of warehouses, trucks and a delivery route"></div>
  <h2 class="abs about-h">ABOUT US</h2>
  <div class="abs about-p">
    <p>Praesent sit amet est in dictum dolor eu dictum porttitor enim felis viverra mi eget luctus massa purus quis odio etiam nulla massa pharetra facilisis volutpat in imperdiet sit amet sem aliquam nec erat at purus cursus interdum vestibulum ligula augue bibendum accumsan.</p>
    <p>Vestibulum ut commodo a mi morbi ornare gravida elit integer congue augue et malesuada iaculis ipsum dui aliquet felis at cursus magna nisl nec elit donec iaculis diam a nisi accumsan viverra duis sed tellus et tortor vestibulum gravida praesent elementum elit at tellus curabitur.</p>
  </div>
</section>

<section class="why">
  <svg class="abs why-band" width="1200" height="550" viewBox="0 0 1200 550">
    <defs><linearGradient id="whyFill" x1="0" y1="0" x2="1" y2="0"><stop offset="0" stop-color="#f2425a"/><stop offset="1" stop-color="#d20f1c"/></linearGradient></defs>
    <polygon points="0,7 1200,90 1200,450 0,545" fill="url(#whyFill)"/>
  </svg>
  <h2 class="abs why-h">WHY CHOOSE US</h2>
  <p class="abs why-intro">Aipsum dui aliquet felis at cursus magna nisl nec elit donec iaculis diam a nisi accumsan viverra duis sed tellus et tortor vestibulum gravida</p>
  <ul class="abs why-list">
    <li>Duis sed tellus et tortor vestibulum gravida</li>
    <li>Praesent elementum elit at tellus</li>
    <li>Curabitur metus ipsum luctus eu malesuada</li>
    <li>Pt tincidunt sed diam Donec quis mi</li>
    <li>Sed magna hendrerit accumsan Suspendisse</li>
  </ul>
  <div class="abs why-photo" role="img" aria-label="Photo of boxed goods stacked on pallets in a warehouse store"></div>
</section>

<section class="process">
  <h2 class="abs process-h">OUR PROCESS</h2>
  <div class="abs step-ring" style="left:195px;top:1849px"><svg width="56" height="56" viewBox="0 0 56 56" fill="none" stroke="#888" stroke-width="3"><path d="M28 6l20 10v24L28 50 8 40V16z"/><path d="M8 16l20 10 20-10M28 26v24"/></svg></div>
  <div class="abs step-ring active" style="left:530px;top:1849px"><svg width="60" height="56" viewBox="0 0 60 56" fill="none" stroke="#fff" stroke-width="3"><path d="M4 8h10l8 30h28l6-20"/><rect x="24" y="12" width="10" height="10" fill="#fff"/><rect x="36" y="16" width="10" height="8" fill="#fff"/><circle cx="26" cy="46" r="4"/><circle cx="46" cy="46" r="4"/></svg></div>
  <div class="abs step-ring" style="left:863px;top:1849px"><svg width="64" height="48" viewBox="0 0 64 48" fill="none" stroke="#888" stroke-width="3"><rect x="4" y="6" width="36" height="28"/><path d="M40 16h12l8 10v8H40z"/><circle cx="16" cy="38" r="5" fill="#fff"/><circle cx="50" cy="38" r="5" fill="#fff"/></svg></div>
  <div class="abs step-line"></div>
  <span class="abs step-node" style="left:251px;top:2007px"></span>
  <span class="abs step-node" style="left:586px;top:2007px;border-color:#333;border-width:4px"></span>
  <span class="abs step-node" style="left:919px;top:2007px"></span>
  <h3 class="abs step-title" style="left:91px;top:2062px">PACKING PRODUCTS</h3>
  <h3 class="abs step-title" style="left:426px;top:2062px">SUPPLY PRODUCT</h3>
  <h3 class="abs step-title" style="left:759px;top:2062px">DELIVERY</h3>
  <p class="abs step-text" style="left:91px;top:2098px">Lorem ipsum dolor sit amet con-<br>sectetuer adipiscing elit</p>
  <p class="abs step-text" style="left:426px;top:2098px">Lorem ipsum dolor sit amet con-<br>sectetuer adipiscing elit</p>
  <p class="abs step-text" style="left:759px;top:2098px">Lorem ipsum dolor sit amet con-<br>sectetuer adipiscing elit</p>
</section>

<section class="news">
  <svg class="abs news-band" width="1200" height="710" viewBox="0 0 1200 710" role="img" aria-label="Dark background photo of a truck on a highway">
    <defs><linearGradient id="newsFill" x1="0" y1="0" x2="0" y2="1"><stop offset="0" stop-color="#3a3a3a"/><stop offset=".5" stop-color="#6a6a6a"/><stop offset="1" stop-color="#1e1e1e"/></linearGradient></defs>
    <polygon points="0,115 1200,0 1200,705 0,565" fill="url(#newsFill)"/>
  </svg>
  <h2 class="abs news-h">NEWS &amp; BLOGS</h2>
  <article class="abs card photo" style="left:119px" role="img" aria-label="Photo of two warehouse workers reviewing a tablet">
    <p class="cap">Curabitur iaculis tempus eros<br>Curabitur vel mi sit amet</p>
  </article>
  <article class="abs card feature" style="left:447px">
    <p class="date">| 25 MARCH 2018</p>
    <h3>Donec dictum lectus non odio<br>Cras ante vitae enim</h3>
    <p>Ullamcorper est eget tempor cursus neque mi consectetuer mi a ultricies massa est sed nisl class aptent taciti sociosqu ad litora torquent per conubia nostra</p>
    <span class="more">READ MORE</span>
  </article>
  <article class="abs card photo" style="left:771px;background:linear-gradient(180deg,#a58d72,#7b6650 60%,#3a3128)" role="img" aria-label="Photo of cardboard boxes on warehouse racks">
    <p class="cap">Curabitur iaculis tempus eros<br>Curabitur vel mi sit amet</p>
  </article>
</section>

<section class="testimonials">
  <h2 class="abs testi-h">TESTIMONIALS</h2>
  <blockquote class="abs quote-card" style="left:119px">
    <p class="q">Ullamcorper est eget tempor cursus neque mi consectetuer mi a ultricies massa est sed nisl class aptent taciti sociosqu ad litora torquent per conubia nostra per</p>
    <div class="author"><span class="avatar" role="img" aria-label="Author portrait"></span><div><b>By Author Name</b><small>Marketing Manager</small></div></div>
  </blockquote>
  <blockquote class="abs quote-card" style="left:616px">
    <p class="q">Ullamcorper est eget tempor cursus neque mi consectetuer mi a ultricies massa est sed nisl class aptent taciti sociosqu ad litora torquent per conubia nostra per</p>
    <div class="author"><span class="avatar" role="img" aria-label="Author portrait"></span><div><b>By Author Name</b><small>Marketing Manager</small></div></div>
  </blockquote>
  <div class="abs testi-dots"><span class="arrow-dot"></span><span class="dot" style="background:#777"></span><span class="dot"></span><span class="dot"></span><span class="dot"></span><span class="arrow-dot"></span></div>
</section>

<footer>
  <svg class="abs footer" width="1200" height="505" viewBox="0 0 1200 505">
    <defs><linearGradient id="footFill" x1="0" y1="0" x2="0" y2="1"><stop offset="0" stop-color="#dcdcdc"/><stop offset=".3" stop-color="#f2f2f2"/><stop offset="1" stop-color="#e4e4e4"/></linearGradient></defs>
    <polygon points="0,0 1200,55 1200,505 0,505" fill="url(#footFill)"/>
  </svg>
  <div class="abs foot-brand"><i></i>MARLOW</div>
  <div class="abs foot-col" style="left:127px"><h4>COMPANY</h4><ul><li>Home</li><li>About Us</li><li>Our Process</li><li>How It Work</li><li>Why Us</li></ul></div>
  <div class="abs foot-col" style="left:353px"><h4>SUBLINKS</h4><ul><li>Products</li><li>Wholesale</li><li>Our Team</li><li>Testimonials</li></ul></div>
  <div class="abs foot-col" style="left:586px"><h4>RESOURCES</h4><ul><li>XML Site map</li><li>Privacy Policy</li><li>Term of Use</li><li>Contact Us</li></ul></div>
  <div class="abs foot-col contact" style="left:786px"><h4>CONTACT US</h4><ul>
    <li><svg width="14" height="18" viewBox="0 0 14 18"><path d="M7 0a7 7 0 0 1 7 7c0 5-7 11-7 11S0 12 0 7a7 7 0 0 1 7-7z" fill="#ec1f27"/><circle cx="7" cy="7" r="2.5" fill="#fff"/></svg>42 Harbor Lane #5 Texas 10024 TX</li>
    <li><svg width="16" height="16" viewBox="0 0 24 24"><path fill="none" stroke="#ec1f27" stroke-width="2" d="M6.6 10.8a15 15 0 0 0 6.6 6.6l2.2-2.2a1 1 0 0 1 1-.25 11.4 11.4 0 0 0 3.6.57 1 1 0 0 1 1 1V20a1 1 0 0 1-1 1A17 17 0 0 1 3 4a1 1 0 0 1 1-1h3.5a1 1 0 0 1 1 1c0 1.25.2 2.45.57 3.6a1 1 0 0 1-.25 1z"/></svg>986 555 2250</li>
    <li><svg width="16" height="12" viewBox="0 0 24 18"><rect x="1" y="1" width="22" height="16" fill="none" stroke="#ec1f27" stroke-width="2"/><path d="M1 1l11 9 11-9" fill="none" stroke="#ec1f27" stroke-width="2"/></svg>hello@marlowimports.com</li>
  </ul></div>
  <div class="abs foot-rule"></div>
  <p class="abs copy">© 2018 Company Name  All right reserved</p>
  <div class="abs social"><span></span><span></span><span></span><span></span></div>
</footer>

</body>
</html>
```